Australian IT Company requires Business Card Design

Bluefinch is an Australian company that specialises in IT consulting & support, software development, project management, network services.

We have been in business for 15 years.

* We require a business card with the following on it:
Logo
Address
Contact Details
Space for staff name, title & mobile number

Industry/Entity Type

Software

```html
<!DOCTYPE html>
<html lang="en">
<head>
<meta charset="utf-8">
<title>Bluefinch Business Card</title>
<link rel="stylesheet" href="https://fonts.googleapis.com/css2?family=Montserrat:wght@400;600;700&family=Open+Sans:wght@400;600&display=swap">
<style>
  :root {
    --brand-blue: #3b6e99;
    --brand-grey: #6d6e71;
    --ink: #2b2b2b;
    --paper: #ffffff;
    --backdrop: #e9ebee;
    --rule: #333333;
  }
  * { box-sizing: border-box; margin: 0; padding: 0; }
  html, body { width: 1200px; height: 680px; overflow: hidden; }
  body {
    background: var(--backdrop);
    font-family: "Open Sans", Arial, sans-serif;
    color: var(--ink);
    position: relative;
  }
  .card {
    position: absolute;
    top: 185px;
    width: 540px;
    height: 309px;
    overflow: hidden;
    box-shadow: 0 6px 18px rgba(0,0,0,0.18);
  }
  .card--front { left: 40px; background: var(--paper); }
  .card--back  { left: 620px; background: var(--brand-blue); }

  /* Brand lockup */
  .brand { position: absolute; display: flex; align-items: center; gap: 14px; white-space: nowrap; }
  .brand__square { width: 40px; height: 40px; flex: none; }
  .brand__text { flex: none; }
  .brand__name {
    font-family: "Montserrat", Arial, sans-serif;
    font-weight: 700;
    font-size: 34px;
    line-height: 1;
    letter-spacing: 0.5px;
  }
  .brand__tagline {
    font-family: "Open Sans", Arial, sans-serif;
    font-weight: 400;
    font-size: 10px;
    letter-spacing: 1px;
    margin-top: 6px;
    white-space: nowrap;
  }

  .card--front .brand { left: 28px; top: 48px; }
  .card--front .brand__square { background: var(--brand-blue); }
  .card--front .brand__name { color: var(--brand-blue); }
  .card--front .brand__tagline { color: var(--brand-grey); }

  .front__rule {
    position: absolute; left: 82px; right: 28px; top: 118px;
    height: 1px; background: var(--rule);
  }

  .staff { position: absolute; left: 28px; top: 146px; }
  .staff__name { font-size: 17px; font-weight: 400; color: var(--ink); }
  .staff__title { font-size: 11.5px; color: var(--ink); margin-top: 1px; }
  .staff__underline {
    margin-top: 5px; width: 190px; height: 2px; background: var(--brand-blue);
  }

  .contact {
    position: absolute; right: 28px; top: 140px;
    list-style: none; font-size: 11.5px; line-height: 1;
  }
  .contact__item { display: flex; align-items: center; gap: 8px; margin-bottom: 5px; white-space: nowrap; }
  .contact__icon { width: 11px; height: 11px; flex: none; }

  .address {
    position: absolute; left: 28px; bottom: 44px;
    font-style: normal; font-size: 13px; line-height: 1.3;
  }

  .front__band { position: absolute; left: 0; bottom: 0; width: 540px; height: 26px; }

  .card--back .brand {
    left: 50%; top: 108px; transform: translateX(-50%);
  }
  .card--back .brand__square { background: var(--paper); }
  .card--back .brand__name { color: var(--paper); }
  .card--back .brand__tagline { color: var(--paper); }
  .back__web {
    position: absolute; left: 0; right: 0; bottom: 66px;
    text-align: center; color: var(--paper);
    font-size: 12px; letter-spacing: 4px;
  }
</style>
</head>
<body>

<section class="card card--front" aria-label="Business card front">
  <div class="brand">
    <div class="brand__square"></div>
    <div class="brand__text">
      <div class="brand__name">BLUEFINCH</div>
      <div class="brand__tagline">Technology Built Around You</div>
    </div>
  </div>

  <div class="front__rule"></div>

  <div class="staff">
    <div class="staff__name">Liam Carver</div>
    <div class="staff__title">Manager</div>
    <div class="staff__underline"></div>
  </div>

  <ul class="contact">
    <li class="contact__item">
      <svg class="contact__icon" viewBox="0 0 12 12" aria-hidden="true"><path d="M3 1l2 2.5-1.2 1.2c.6 1.4 1.6 2.4 3 3L8 6.5 10.5 8.5 9.5 10.8C5 10.5 1.5 7 1.2 2.5z" fill="var(--brand-blue)"/></svg>
      <span>+61 3 9000 1234</span>
    </li>
    <li class="contact__item">
      <svg class="contact__icon" viewBox="0 0 12 12" aria-hidden="true"><rect x="3" y="0.5" width="6" height="11" rx="1" fill="var(--brand-blue)"/><rect x="4" y="2" width="4" height="6.5" fill="#fff"/></svg>
      <span>+61 3 9000 5678</span>
    </li>
    <li class="contact__item">
      <svg class="contact__icon" viewBox="0 0 12 12" aria-hidden="true"><rect x="0.5" y="2.5" width="11" height="7.5" fill="var(--brand-blue)"/><path d="M0.5 2.5L6 7l5.5-4.5" fill="none" stroke="#fff" stroke-width="1"/></svg>
      <span>liam@bluefinch.net.au</span>
    </li>
    <li class="contact__item">
      <svg class="contact__icon" viewBox="0 0 12 12" aria-hidden="true"><circle cx="6" cy="6" r="5.2" fill="none" stroke="var(--brand-blue)" stroke-width="1.2"/><ellipse cx="6" cy="6" rx="2.2" ry="5.2" fill="none" stroke="var(--brand-blue)" stroke-width="1"/><path d="M1 6h10M2 3.5h8M2 8.5h8" stroke="var(--brand-blue)" stroke-width="0.9"/></svg>
      <span>www.bluefinch.net.au</span>
    </li>
  </ul>

  <address class="address">
    14 Harbour Lane<br>
    Unit 5<br>
    Carlton Vic 3053
  </address>

  <svg class="front__band" viewBox="0 0 540 26" aria-hidden="true">
    <polygon points="250,26 290,4 540,4 540,26" fill="var(--brand-grey)"/>
    <rect x="0" y="18" width="540" height="8" fill="var(--brand-blue)"/>
  </svg>
</section>

<section class="card card--back" aria-label="Business card back">
  <div class="brand">
    <div class="brand__square"></div>
    <div class="brand__text">
      <div class="brand__name">BLUEFINCH</div>
      <div class="brand__tagline">Technology Built Around You</div>
    </div>
  </div>
  <div class="back__web">www.bluefinch.net.au</div>
</section>

</body>
</html>
```